Lantern Crest Pathway

I need a on page electronic flyer for this coaching program. I want a silhouette to accompany the case the copy starts with. I have the copy written but need it put together in a striking way.

Target Market(s)

towards higher net worth individuals

Industry/Entity Type

Electronic

```html
<!DOCTYPE html>
<html lang="en">
<head>
<meta charset="utf-8">
<title>Lantern Crest Pathway</title>
<link rel="stylesheet" href="https://fonts.googleapis.com/css2?family=Arimo:wght@400;700&family=Tinos:wght@700&display=swap">
<style>
  :root {
    --title-blue: #1d1fd6;
    --ink: #111111;
    --headline-orange: #e8701e;
    --band-yellow: #f6c500;
    --band-orange: #f47a1f;
    --curve-blue: #2aa8e6;
    --badge-blue: #2b8de0;
    --bar-teal: #3ccf8c;
    --bar-purple: #9a1ee0;
    --bar-red: #c7230f;
    --bar-olive: #9d9913;
    --bar-green: #62df1e;
    --bar-blue: #6a93ee;
    --white: #ffffff;
  }
  * { margin: 0; padding: 0; box-sizing: border-box; }
  html, body { width: 1200px; height: 911px; overflow: hidden; background: var(--white); }
  .flyer { position: relative; width: 1200px; height: 911px; font-family: "Arimo", Arial, sans-serif; color: var(--ink); }
  .tagline {
    position: absolute; top: 22px; left: 0; width: 100%; text-align: center;
    font-family: "Tinos", "Times New Roman", serif; font-weight: 700; font-size: 38px;
    color: var(--title-blue);
  }
  .top-rule { position: absolute; left: 38px; top: 79px; width: 1128px; height: 11px; background: var(--ink); }
  .case-photo {
    position: absolute; left: 38px; top: 90px; width: 412px; height: 560px;
    background: linear-gradient(160deg, #d9dde0 0%, #9aa4ab 35%, #3b3f44 65%, #1b1c1f 100%);
  }
  .backdrop { position: absolute; left: 0; top: 0; width: 1200px; height: 911px; }
  .badge { position: absolute; left: 70px; top: 490px; width: 132px; height: 132px; border-radius: 50%;
    background: var(--badge-blue); display: flex; align-items: center; justify-content: center; text-align: center;
    color: var(--white); font-size: 19px; font-weight: 700; line-height: 1.1; }
  .headline { position: absolute; left: 488px; top: 118px; font-size: 27px; font-weight: 700; color: var(--headline-orange); }
  .subhead { position: absolute; left: 532px; top: 157px; font-size: 25px; font-weight: 700; color: var(--headline-orange); }
  .story { position: absolute; left: 477px; top: 210px; width: 685px; font-size: 14.6px; line-height: 17.6px; }
  .story p { margin-bottom: 17.6px; }
  .story p.tight { margin-bottom: 0; }
  .program-title { position: absolute; left: 57px; top: 645px; font-family: "Tinos", "Times New Roman", serif; font-weight: 700; font-size: 18px; }
  .bar { position: absolute; left: 50px; height: 24px; padding-left: 10px; display: flex; align-items: center;
    color: var(--white); font-size: 12.6px; font-weight: 700; border: 1px solid rgba(255,255,255,0.7); }
  .bar::before { content: "\27A4"; margin-right: 6px; font-size: 11px; }
  .bar.outcome { width: 522px; }
  .bar.offer { width: 640px; font-size: 13.4px; }
  .teal { top: 667px; background: var(--bar-teal); }
  .purple { top: 694px; background: var(--bar-purple); }
  .red { top: 720px; background: var(--bar-red); }
  .olive { top: 745px; background: var(--bar-olive); }
  .green { top: 801px; background: var(--bar-green); }
  .blue { top: 828px; background: var(--bar-blue); }
  .bio { position: absolute; right: 40px; top: 773px; text-align: right; }
  .bio-name { font-size: 15px; font-weight: 700; margin-bottom: 8px; }
  .bio-line { font-size: 12.6px; line-height: 26px; }
</style>
</head>
<body>
<div class="flyer">
  <h1 class="tagline">Sometimes the best financial advice isn't about numbers...</h1>
  <div class="top-rule"></div>
  <div class="case-photo" role="img" aria-label="Silhouette of a worried man sitting with his head in his hand beside a window overlooking the sea"></div>

  <svg class="backdrop" viewBox="0 0 1200 911" aria-hidden="true">
    <path d="M38 612 Q 560 560 1166 668 L1166 873 L38 873 Z" fill="var(--band-yellow)"/>
    <path d="M38 612 Q 560 560 1166 668" fill="none" stroke="var(--curve-blue)" stroke-width="5"/>
    <path d="M38 620 Q 560 570 1166 676" fill="none" stroke="var(--white)" stroke-width="4"/>
    <path d="M560 873 Q 860 770 1166 686 L1166 873 Z" fill="var(--band-orange)"/>
    <path d="M600 860 Q 880 765 1166 682" fill="none" stroke="var(--ink)" stroke-width="3"/>
  </svg>

  <div class="badge">Crestline<br>Circle</div>

  <h2 class="headline">Lantern Crest Pathway</h2>
  <h3 class="subhead">From Financial Worries to Wealth Satisfaction</h3>

  <div class="story">
    <p>A 49 year old attorney, Steve was used to success and rising net worth. But with huge losses in the market crash, layoffs at his firm, his kids heading for college and the stagnant economy stretching ahead, his usual optimism is gone. With his anxiety growing, Steve doubts his own decision making ability. His confidence slipping, he stopped opening his financial statements and could barely speak to his financial advisor. He thought if his advisor said “hang in there” one more time, he just might blow up.</p>
    <p>Yet Steve felt too embarrassed to talk about his deep worries, even with his wife. It seemed like all he could do was pour another glass of wine and suffer in isolation. If you're like Steve, you're afraid and alone with plenty of company. In a September 2009 Northfield Psychology Council poll, 80 percent reported the economy is causing significant stress, up from 66 percent from the previous April. The National Rest Institute said 27 percent of people surveyed had sleeplessness because of economic anxiety.</p>
    <p class="tight">This process guides you to step back and understand the source of your financial worry—your unique story about the meaning of money. Your money story drives your emotions and decision making—for better and worse. You'll learn a decision making tool for more conscious, effective and satisfying financial and life decisions.</p>
    <p>You'll also examine your core values and strengths—what really matters most to you and how you work at your best. When you use your money and your core strengths to pursue your highest aspirations, life and wealth become balanced. As you commit more fully to your mission and passions, satisfaction grows and money worries melt away.</p>
  </div>

  <div class="program-title">A five session program to:</div>
  <div class="bar outcome teal">Learn a decision making tool to make choices that truly serve your needs</div>
  <div class="bar outcome purple">Clarify and more fully engage with your purpose and passions</div>
  <div class="bar outcome red">Improve your relationship with your financial advisor</div>
  <div class="bar outcome olive">Feel more in control and confident in your financial life</div>

  <div class="bar offer green">$995 Money back guarantee</div>
  <div class="bar offer blue">For more information, call Dr. Dana Whitfield, 555-014-2290, dana@crestlinecircle.com</div>

  <div class="bio">
    <div class="bio-name">Dana Whitfield, Ph.D</div>
    <div class="bio-line">a psychologist with 30 years of experience</div>
    <div class="bio-line">treating anxiety and stress. She is co-founder and facilitator of</div>
    <div class="bio-line">Crestline Circle, a peer learning group for high net worth investors.</div>
  </div>
</div>
</body>
</html>
```